Packaging card Design

we are going to offer a general assortment of action cam mounts. currently all action/sports cam vendors offer their assortment of mounts, we want to offer 1 assortment suitable for all major brands.
here we will request 1 topcard for the (bag) package, but the total job will be designing 7 to 15 ones (same bbasics, small changes)
please google "zentiq headstrap mount packaging" and you find an image of the original Zentiq packaging (carton top with plastic bag). we need the design of the topcard.
description:
FRONT:
- create VEX-grip logo (to be placed on top of card)
- product name (in this example the Head Strap)
- suitable for:
* Zentiq
* UBT Lumivex / Ventaqo
* Bolna HD
* Veltrim
* oKEL / uZA / RASO
* Tavek / QMR
* Sable Orchard Nuo
BACK:
in centre a drawing of the item with a camera (Zentiq Falk7) mounted on it. only the line drawing of the headstrap must be bold and the cam light..
around it we mention all the brands mentioned on the front and mention it is compatible in 4 languages (English / French / Dutch / German.
so what we get is:
Zentiq:
Compatible
Kompatibel
(for other accesories we might state here that a 'tripod mount' is needed to fit)
+ we mention the URL www.VEX-grips.eu
color scheme can be either Zentiq style (black + logo blue/white) or you can create your own mixture (please do not forget the BLACK & blue & white of Zentiq is recognisable).
Reason: we started the project late due to Briefnest authorisation and many of you just recently accepted the offer, next to that we made it a guaranteed project yesterday so this prolongation gives you more time to submit.
kind regards,
Tobias
Zentiq clients (sportive, but more over getting a mainstreme product)
Plastic

```html
<!DOCTYPE html>
<html lang="en">
<head>
<meta charset="utf-8">
<title>VEX-grip Head Strap – Top Card</title>
<link rel="stylesheet" href="https://fonts.googleapis.com/css2?family=Quicksand:wght@300;500&display=swap">
<style>
  :root {
    --card-navy: #283744;
    --ink-white: #ffffff;
    --brand-blue: #1fa0e0;
  }
  html, body {
    margin: 0;
    padding: 0;
    width: 1200px;
    height: 561px;
    overflow: hidden;
    background: var(--card-navy);
  }
  .top-card {
    position: relative;
    width: 1200px;
    height: 561px;
    overflow: hidden;
    background: var(--card-navy);
    color: var(--ink-white);
    font-family: "Quicksand", sans-serif;
  }
  .hang-hole {
    position: absolute;
    left: 476px;
    top: 65px;
    width: 247px;
    height: 80px;
  }
  .brand {
    position: absolute;
    right: 53px;
    top: 170px;
    display: flex;
    align-items: center;
    gap: 20px;
  }
  .brand-mark {
    width: 24px;
    height: 24px;
    background: var(--brand-blue);
  }
  .brand-name {
    margin: 0;
    font-weight: 500;
    font-size: 76px;
    line-height: 1;
    letter-spacing: 1px;
    color: var(--ink-white);
  }
  .product-name {
    position: absolute;
    left: 72px;
    top: 390px;
    margin: 0;
    font-weight: 300;
    font-size: 72px;
    line-height: 1;
    letter-spacing: 3px;
  }
  .compatibility {
    position: absolute;
    left: 73px;
    top: 487px;
    margin: 0;
    font-weight: 300;
    font-size: 24px;
    line-height: 1;
    letter-spacing: 0.5px;
  }
</style>
</head>
<body>
  <main class="top-card">
    <svg class="hang-hole" viewBox="0 0 247 80" aria-hidden="true">
      <path fill="#ffffff" d="M24 32 H100 A24 24 0 0 1 148 32 H223 A24 24 0 0 1 223 80 H24 A24 24 0 0 1 24 32 Z"/>
    </svg>

    <div class="brand">
      <span class="brand-mark" aria-hidden="true"></span>
      <p class="brand-name">VEX-grip</p>
    </div>

    <h1 class="product-name">Head Strap</h1>
    <p class="compatibility">Compatible with all major action cameras</p>
  </main>
</body>
</html>
```